Graphics for Verdaxa telehealth weight loss plans

Verdaxa focuses on delivering medical weight-loss using prescription medicine and telehealth consults. Verdaxa needs graphics for its ecommerce site for three weight loss plans. The plans are posted here with current graphics and descriptions of what is included with each plan. Please do not feel constrained by current graphics or styling.

- https://store.verdaxahealth.com/products/radiant-horizon-plan
- https://store.verdaxahealth.com/products/medication-kickstart-plan
- https://store.verdaxahealth.com/products/balanced-ascent-plan

The graphics need to look good on mobile and desktop browsers.

```html
<!DOCTYPE html>
<html lang="en">
<head>
<meta charset="utf-8">
<title>Radiant Horizon Plan – Verdaxa</title>
<link rel="stylesheet" href="https://fonts.googleapis.com/css2?family=Assistant:wght@400;600;700&family=Oswald:wght@400;500;600&display=swap">
<style>
  :root{
    --ink:#121212;
    --ink-soft:#3d3d3d;
    --paper:#ffffff;
    --brand-blue:#2e4c9e;
    --brand-white:#ffffff;
    --accent-green:#b7cdb5;
    --photo-dark:#5a5a5a;
    --photo-light:#c9c9c9;
  }
  *{box-sizing:border-box;margin:0;padding:0}
  html,body{width:1200px;height:837px;overflow:hidden;background:var(--paper)}
  body{position:relative;font-family:"Assistant",sans-serif;color:var(--ink)}
  .edge{position:absolute;left:0;width:1200px;height:2px;background:var(--accent-green)}
  .edge--top{top:0}
  .edge--bottom{bottom:0;height:4px}

  /* header */
  .site-header{position:absolute;left:0;top:0;width:1200px;height:140px}
  .brand{position:absolute;left:63px;top:63px;display:flex;align-items:center;gap:6px;font-size:14.5px;font-weight:700;letter-spacing:.2px;line-height:20px;color:var(--ink)}
  .brand__mark{width:11px;height:11px;border:1.6px solid var(--ink)}
  .nav{position:absolute;top:63px;left:152px;height:22px;font-size:15px;letter-spacing:.6px;line-height:22px;color:var(--ink-soft)}
  .nav a{color:inherit;text-decoration:none;position:absolute;top:0;white-space:nowrap}
  .nav .caret{display:inline-block;margin-left:6px;vertical-align:2px}
  .header-icons{position:absolute;top:60px;left:1030px;width:130px;height:28px}
  .header-icons svg{position:absolute;top:0}

  /* product graphic */
  .plan-graphic{position:absolute;left:52px;top:144px;width:496px;height:642px;background:var(--brand-blue);overflow:hidden;color:var(--brand-white);font-family:"Oswald",sans-serif}
  .plan-graphic__photo{position:absolute}
  .photo-body{left:0;top:0;width:380px;height:141px;background:linear-gradient(160deg,#8d8d8d,var(--photo-dark) 60%,#3b3b3b)}
  .photo-capsules{left:380px;top:0;width:116px;height:206px;background:linear-gradient(200deg,#e3e3e3,var(--photo-light) 50%,#8f8f8f)}
  .plan-graphic__title{position:absolute;left:31px;top:146px;font-size:47px;font-weight:600;line-height:56px;letter-spacing:.4px;text-transform:uppercase}
  .plan-graphic__subtitle{position:absolute;left:37px;top:271px;font-size:25px;font-weight:400;line-height:31px;text-transform:uppercase;letter-spacing:.2px}
  .plan-graphic__tag{position:absolute;left:38px;top:350px;background:var(--brand-white);color:var(--brand-blue);font-size:17px;font-weight:600;padding:0 10px;height:27px;line-height:27px;border-radius:2px}
  .feature{position:absolute;font-size:19.5px;font-weight:500;line-height:23px;padding-left:10px;white-space:nowrap}
  .feature::before{content:"•";position:absolute;left:0;font-size:16px}
  .feature small{font-size:15px;font-weight:400}
  .feature .note{display:block;font-size:15px;font-weight:400;line-height:20px;margin-left:4px}
  .plan-graphic__billing{position:absolute;left:33px;top:548px;display:flex;align-items:center}
  .billing-icon{width:54px;height:54px;border-radius:50%;background:var(--brand-white);display:flex;align-items:center;justify-content:center;position:relative;z-index:1}
  .billing-label{background:var(--brand-white);color:#1a2a5c;font-size:17.5px;font-weight:500;height:27px;line-height:27px;padding:0 15px 0 14px;margin-left:-2px;border-radius:0 2px 2px 0}

  /* product info */
  .product-info{position:absolute;left:602px;top:150px;width:560px}
  .product-info__title{font-size:44px;font-weight:400;line-height:58px;letter-spacing:.4px;min-height:116px}
  .product-info__price{margin-top:14px;font-size:17.5px;letter-spacing:1px}
  .product-info__recurring{margin-top:25px;font-size:17.5px;color:var(--ink-soft);letter-spacing:.5px}
  .product-info__control{margin-top:20px;font-size:16px;color:var(--ink-soft);letter-spacing:.6px}
  .buy-button{display:block;margin-top:26px;width:481px;height:53px;background:var(--ink);color:var(--paper);border:0;font-family:inherit;font-size:15.5px;letter-spacing:1.2px}
  .product-info__body{margin-top:33px;width:548px;font-size:16.5px;line-height:32px;color:var(--ink-soft);letter-spacing:.4px}
  .product-info__body p{margin-bottom:17px}
  .product-info__body strong{color:#2a2a2a;font-weight:700}
</style>
</head>
<body>
  <div class="edge edge--top"></div>

  <header class="site-header">
    <div class="brand"><span class="brand__mark"></span>Verdaxa</div>
    <nav class="nav">
      <a style="left:0">Testimonials</a>
      <a style="left:115px">Help<svg class="caret" width="10" height="6" viewBox="0 0 10 6"><path d="M1 1l4 4 4-4" fill="none" stroke="#3d3d3d" stroke-width="1.4"/></svg></a>
      <a style="left:190px">About</a>
      <a style="left:258px">Contact</a>
    </nav>
    <div class="header-icons">
      <svg style="left:0" width="26" height="26" viewBox="0 0 26 26"><circle cx="10.5" cy="10.5" r="8" fill="none" stroke="#121212" stroke-width="1.8"/><path d="M16.5 16.5l7 7" stroke="#121212" stroke-width="1.8"/></svg>
      <svg style="left:49px" width="24" height="26" viewBox="0 0 24 26"><circle cx="12" cy="8" r="5.5" fill="none" stroke="#121212" stroke-width="1.8"/><path d="M2 24.5c0-5 4-8 10-8s10 3 10 8z" fill="none" stroke="#121212" stroke-width="1.8"/></svg>
      <svg style="left:96px" width="26" height="26" viewBox="0 0 26 26"><path d="M3 7h20v15a2 2 0 0 1-2 2H5a2 2 0 0 1-2-2z" fill="none" stroke="#121212" stroke-width="1.8"/><path d="M8.5 9V6a4.5 4.5 0 0 1 9 0v3" fill="none" stroke="#121212" stroke-width="1.8"/></svg>
    </div>
  </header>

  <section class="plan-graphic">
    <div class="plan-graphic__photo photo-body" role="img" aria-label="Black and white photo of a fit muscular torso"></div>
    <div class="plan-graphic__photo photo-capsules" role="img" aria-label="Black and white photo of scattered medication capsules"></div>
    <h2 class="plan-graphic__title">Radiant<br>Horizon Plan</h2>
    <p class="plan-graphic__subtitle">Physician Consultation<br>Phentermine Program</p>
    <span class="plan-graphic__tag">Includes</span>

    <div class="feature" style="left:27px;top:392px">100% online.<span class="note">No need to visit the office.</span></div>
    <div class="feature" style="left:32px;top:446px">1 month supply. <small>(30 pills)</small></div>
    <div class="feature" style="left:27px;top:477px">Custom crafted diet plan<br>to achieve your goals.</div>
    <div class="feature" style="left:237px;top:388px">Real Phentermine <small>(37.5mg/Pill)</small><br>delivered to your door.</div>
    <div class="feature" style="left:241px;top:446px">Expert nutrition consult.</div>
    <div class="feature" style="left:237px;top:477px">Nutrition coaching to improve<br>your health and vitality.</div>

    <div class="plan-graphic__billing">
      <div class="billing-icon">
        <svg width="34" height="32" viewBox="0 0 34 32"><rect x="7" y="5" width="20" height="13" rx="2" fill="none" stroke="#1a2a5c" stroke-width="1.6"/><path d="M7 9h20" stroke="#1a2a5c" stroke-width="1.6"/><path d="M4 20a13 9 0 0 0 24 4" fill="none" stroke="#1a2a5c" stroke-width="1.6"/><path d="M24 21l4 3-4 3" fill="none" stroke="#1a2a5c" stroke-width="1.6"/></svg>
      </div>
      <span class="billing-label">Month-to-month pay as you go.</span>
    </div>
  </section>

  <main class="product-info">
    <h1 class="product-info__title">Radiant Horizon Plan</h1>
    <p class="product-info__price">$199.00</p>
    <p class="product-info__recurring">No recurring billing</p>
    <p class="product-info__control">You're always in control of when you reorder.</p>
    <button class="buy-button">Buy it now</button>
    <div class="product-info__body">
      <p>The <strong>Radiant Horizon Plan</strong> includes <strong>real Phentermine (37.5mg / pill)</strong>. You get a 1 month supply (30 pills, 1 pill per day).</p>
      <p>In addition to Phentermine, this pay as you go plan provides you with a <strong>consultation with a nutrition expert</strong> to custom craft the perfect plan for you.</p>
      <p>This program is designed for people who need some help with caloric restriction, and also want to take the guess-work out of their eating plan. There are huge benefits to expert nutritionist guidance and support to not only achieve your weight loss goals but also to</p>
    </div>
  </main>

  <div class="edge edge--bottom"></div>
</body>
</html>
```